Im want a website LIKE VRX's and FleetHollow.com's with product payment options like Trenzo's

I need a website LIKE VRX with a header made EXACTLY LIKE THAT OF FLEETHOLLOWS .

The front page photo should be like that of FLEETHOLLOW's webpage as well.

The name of the website will be called "M.K. (Caldera Key)".

We will be targeting ALL MARKETS in a small town in central Panama and charging businesses "listing fees" like a phone book does but also providing informational blogs, news, and other interesting activities.

THIS IS A MULTI PAGE WEBSITE

THIS IS WHERE VRX's website meets Brivelle/FleetHollow.

Once the layout is built I will tweak and modify, add information, and upload items for sale.

Here is a list of specific categories that should be listed out above the front page header image/search bar

-- Home -- News -- Travel -- Activities -- Shop & Dine -- Store -- More... --

These categories should be spread across the bottom of the page in three sections:

WHATS SO GREAT ABOUT (Caldera Key),
HAND PICKED TOURS
ACTIVITIES etc.

Also lets use www.Trenzo.example 's
"HOT DESTINATIONS"
"BEAT THE BEST PRICES IN BOQUETE"
"OCTOBERS INSIDER PICKS"
"TOP DESTINATIONS"
and spread them in four sections side-by-side near the bottom of the page.

Overall I would like to see the finished product to be something LIKE VRX's and FleetHollows.

WE NEED ONLINE PAYMENT OPTIONS LIKE BRIVELLE'S WEBSITE HAS

This will be a desktop website but should be very mobile friendly as well.

-rodmund

P.S. Good luck!

If it isn't already too late to change the website name, the name of the website should be "Caldera Key". Added Friday, October 9, 2015

What do you guys think the budget should be to win this? Added Saturday, October 10, 2015

www.palmorra.example is the most amazing simple site. Whoever can make me a replica with my specifications will win immediately!!!! Added Sunday, October 18, 2015

OMG www.palmorra.example is the bomb!So simple and elegant. Whoever can make me an EXACT REPLICA OF WWW.PALMORRA.EXAMPLE as my site with the specifications mentioned in my brief will take home the $825.00 immediately! Good luck amigos! Added Sunday, October 18, 2015

Does anybody know how to add recurring monthly billing options on this website? Added Sunday, October 18, 2015

ALL MARKETS

Product

Coded - Design and coding required

5+ page

• Coinvey payment options.
• I must be able to add and remove photos/text and video from the HTML files in the page.
• Be creative my friends, and may the odds be forever in your favor!
• I added some photos of a good layout for our page below.

```html
<!DOCTYPE html>
<html lang="en">
<head>
<meta charset="utf-8">
<title>Caldera Key</title>
<link href="https://fonts.googleapis.com/css2?family=Roboto:wght@300;400;500;700&display=swap" rel="stylesheet">
<style>
:root{
  --teal:#1b8db3;
  --teal-dark:#15759a;
  --ink:#333a40;
  --muted:#7d8790;
  --line:#e3e7ea;
  --hero-top:#0c2434;
  --hero-bottom:#16506a;
  --footer:#2a2e33;
  --footer-deep:#1f2226;
  --white:#ffffff;
  --star:#f3b21b;
}
*{box-sizing:border-box;margin:0;padding:0}
html,body{width:705px;height:1200px;overflow:hidden}
body{font-family:"Roboto",Arial,sans-serif;color:var(--ink);background:var(--white);font-size:7px}

/* top strip */
.utility-bar{height:20px;background:rgba(6,22,32,.9);display:flex;align-items:center;justify-content:space-between;padding:0 28px;color:#cfe3ee;font-size:6px}
.utility-bar .group{display:flex;gap:14px;align-items:center}
.utility-bar .pill{border:1px solid #3a5566;padding:2px 6px;border-radius:2px}
.utility-bar .dot{display:inline-block;width:5px;height:5px;border-radius:50%;background:var(--teal);margin-right:3px;vertical-align:middle}

/* hero */
.masthead{position:relative;height:335px;background:linear-gradient(180deg,var(--hero-top),var(--hero-bottom))}
.site-header{height:42px;display:flex;align-items:center;justify-content:space-between;padding:0 28px}
.brand{color:var(--white);font-size:17px;font-weight:500;letter-spacing:.2px}
.main-nav{display:flex;gap:17px}
.main-nav a{color:var(--white);text-decoration:none;font-size:6.5px;font-weight:500;letter-spacing:.3px}
.slider{position:absolute;left:26px;right:26px;top:62px;height:262px;background:linear-gradient(180deg,#9cc6e2 0%,#5aa2c9 30%,#2aa6b3 55%,#19b6b3 75%,#0f8f96 100%)}
.slider-caption{position:absolute;left:0;right:0;top:128px;text-align:center;color:var(--white)}
.slider-caption .kicker{font-size:11px;font-weight:400;letter-spacing:.5px;margin-bottom:4px}
.slider-caption h1{font-size:29px;font-weight:500}
.search-bar{position:absolute;left:176px;top:214px;width:300px;height:22px;background:rgba(0,0,0,.55);display:flex;align-items:center;gap:5px;padding:0 5px}
.search-bar .field{flex:1;height:13px;background:var(--white);font-size:5.5px;color:#8a939a;padding:3px 4px}
.search-bar .btn{width:56px;height:13px;background:var(--teal);color:var(--white);font-size:5.5px;text-align:center;line-height:13px;font-weight:500}
.arrow{position:absolute;top:118px;width:14px;height:14px;border-radius:50%;background:var(--white);display:flex;align-items:center;justify-content:center}
.arrow.left{left:-7px}.arrow.right{right:-7px}

/* welcome */
.welcome{height:250px;text-align:center;padding-top:100px;background:#fbfcfc;border-bottom:1px solid var(--line)}
.welcome h2{font-size:11px;font-weight:500;letter-spacing:.4px;color:var(--ink)}
.welcome .lead{color:var(--teal);font-size:6.5px;margin-top:6px}
.welcome p{width:560px;margin:8px auto 0;color:var(--muted);font-size:5.6px;line-height:10px}
.btn-solid{display:inline-block;margin-top:14px;background:var(--teal);color:var(--white);font-size:5.5px;font-weight:500;padding:6px 14px}

/* tours */
.tours{height:330px;padding:27px 52px 0}
.section-head{display:flex;justify-content:space-between;align-items:center;border-bottom:1px solid var(--line);padding-bottom:9px}
.section-head h3{font-size:9.5px;font-weight:700;letter-spacing:.3px}
.section-head .ctrl{display:flex;gap:6px;color:var(--muted);font-size:9px}
.cards{display:flex;justify-content:space-between;margin-top:22px}
.card{width:181px;height:252px;background:var(--white);box-shadow:0 1px 3px rgba(0,0,0,.15)}
.card .photo{height:126px}
.photo.city{background:linear-gradient(180deg,#1a3a6b,#29558c 55%,#0f2748)}
.photo.pool{background:linear-gradient(180deg,#6b4a2c,#b08457 40%,#2aa6c6 75%,#1c7d9a)}
.photo.beach{background:linear-gradient(180deg,#5fb2e3,#9fd6ee 45%,#e9dcb8 78%,#d4c39a)}
.card .body{padding:10px 9px}
.card .title{color:var(--teal);font-size:6.3px;line-height:10px;font-weight:500}
.rating{margin-top:7px;display:flex;align-items:center;gap:6px;font-size:5.5px;color:var(--muted)}
.stars{color:var(--star);font-size:7px;letter-spacing:1px}
.card .meta{margin-top:10px;display:flex;justify-content:space-between;font-size:5.8px;color:var(--muted)}
.card .price{color:var(--teal);font-weight:700;font-size:7px}

/* feature band */
.features{height:103px;background:var(--teal);display:flex;justify-content:space-between;padding:23px 52px 0;color:var(--white)}
.feature{width:185px;display:flex;gap:10px}
.feature svg{flex:none}
.feature h4{font-size:9px;font-weight:500;margin-bottom:4px}
.feature p{font-size:5.5px;line-height:8px;opacity:.9}
.feature .more{margin-top:3px;font-weight:500;font-size:5.5px}

/* footer */
.site-footer{height:138px;background:var(--footer);display:flex;padding:20px 52px 0;gap:22px;color:#aeb6bd}
.mileage{width:180px;display:flex;gap:9px}
.mileage .badge{width:30px;height:30px;background:#3f4750;flex:none}
.mileage h5{color:var(--white);font-size:6.5px;font-weight:500;margin-bottom:4px}
.mileage p{font-size:5.3px;line-height:8px}
.mileage .btn-solid{margin-top:8px;padding:5px 12px;font-size:5.3px}
.col h5{color:var(--white);font-size:6.5px;font-weight:500;margin-bottom:7px}
.col ul{list-style:none}
.col li{font-size:5.3px;line-height:8.5px}
.col.narrow{width:62px}
.col.search{width:120px;margin-left:auto}
.col.search .input{height:12px;background:var(--white);margin-bottom:5px;font-size:5px;color:#8a939a;padding:3px 4px}
.col.search .btn-solid{margin-top:0;padding:4px 10px;font-size:5px}
.legal{height:22px;background:var(--footer-deep);display:flex;align-items:center;justify-content:space-between;padding:0 52px;color:#8e979f;font-size:5.3px}
.social{display:flex;align-items:center;gap:5px}
.social i{width:7px;height:7px;border-radius:50%;background:#69737c;display:block}
</style>
</head>
<body>

<div class="masthead">
  <div class="utility-bar">
    <div class="group"><span class="pill">USD $</span><span class="pill">English</span></div>
    <div class="group"><span><i class="dot"></i>Login/Register</span><span><i class="dot"></i>My Wish List</span><span><i class="dot"></i>Need a Help?</span></div>
  </div>
  <header class="site-header">
    <div class="brand">Caldera Key</div>
    <nav class="main-nav">
      <a href="#">HOME</a><a href="#">ABOUT</a><a href="#">PLACES</a><a href="#">HOTELS</a><a href="#">BLOG</a><a href="#">CAREERS</a><a href="#">CONTACT</a>
    </nav>
  </header>
  <div class="slider" role="img" aria-label="Tropical lagoon with overwater bungalows and green mountains">
    <div class="arrow left"><svg width="6" height="6" viewBox="0 0 6 6"><path d="M4 0.5 1.5 3 4 5.5" stroke="#333" fill="none" stroke-width="1"/></svg></div>
    <div class="arrow right"><svg width="6" height="6" viewBox="0 0 6 6"><path d="M2 0.5 4.5 3 2 5.5" stroke="#333" fill="none" stroke-width="1"/></svg></div>
    <div class="slider-caption">
      <div class="kicker">Caldera Key</div>
      <h1>in central Panama</h1>
    </div>
    <div class="search-bar">
      <div class="field">Type Your Place...</div>
      <div class="field">Type Your Keywords...</div>
      <div class="btn">SEARCH</div>
    </div>
  </div>
</div>

<section class="welcome">
  <h2>WELCOME TO CALDERA KEY</h2>
  <div class="lead">Simply dummy text of the printing and typesetting industry. Lorem Ipsum has been the industry's standard dummy text</div>
  <p>Sed ut perspiciatis unde omnis iste natus error sit voluptatem accusantium doloremque laudantium, totam rem aperiam, eaque ipsa quae ab illo inventore veritatis et quasi architecto beatae vitae dicta sunt explicabo. Nemo enim ipsam voluptatem quia voluptas sit aspernatur aut odit aut fugit, sed quia consequuntur magni dolores eos qui ratione voluptatem sequi nesciunt. Neque porro quisquam est, qui dolorem ipsum quia dolor sit amet, consectetur, adipisci velit, sed quia non numquam eius modi tempora incidunt ut labore et dolore magnam aliquam quaerat voluptatem.</p>
  <span class="btn-solid">READ MORE</span>
</section>

<section class="tours">
  <div class="section-head">
    <h3>TOURS &amp; SIGHTSEEING</h3>
    <div class="ctrl"><span>&#8249;</span><span>&#8250;</span></div>
  </div>
  <div class="cards">
    <article class="card">
      <div class="photo city" role="img" aria-label="Harbour bridge and city skyline at dusk"></div>
      <div class="body">
        <div class="title">Neque porro quisquam est, qui dolorem ipsum quia dolor sit amet, consectetur...</div>
        <div class="rating"><span class="stars">★★★★★</span>128 Reviews</div>
        <div class="meta"><span>From <span class="price">$88.75</span></span><span>Tour Location</span></div>
      </div>
    </article>
    <article class="card">
      <div class="photo pool" role="img" aria-label="Resort pool at sunset lined with loungers"></div>
      <div class="body">
        <div class="title">Neque porro quisquam est, qui dolorem ipsum quia dolor sit amet, consectetur...</div>
        <div class="rating"><span class="stars">★★★★★</span>128 Reviews</div>
        <div class="meta"><span>From <span class="price">$72.75</span></span><span>Tour Location</span></div>
      </div>
    </article>
    <article class="card">
      <div class="photo beach" role="img" aria-label="White sand beach with palm trees and boat"></div>
      <div class="body">
        <div class="title">Neque porro quisquam est, qui dolorem ipsum quia dolor sit amet, consectetur...</div>
        <div class="rating"><span class="stars">★★★★★</span>128 Reviews</div>
        <div class="meta"><span>From <span class="price">$68.75</span></span><span>Tour Location</span></div>
      </div>
    </article>
  </div>
</section>

<section class="features">
  <div class="feature">
    <svg width="22" height="20" viewBox="0 0 22 20"><path d="M1 4 7 1 15 4 21 1V16L15 19 7 16 1 19Z" fill="none" stroke="#fff" stroke-width="1.6"/><path d="M7 1V16M15 4V19" stroke="#fff" stroke-width="1.4"/></svg>
    <div><h4>Selling guided tours</h4><p>Sure to make you think about a holiday when you follow our guides around every corner.</p><div class="more">More details</div></div>
  </div>
  <div class="feature">
    <svg width="20" height="20" viewBox="0 0 20 20"><rect x="3" y="2" width="14" height="17" fill="none" stroke="#fff" stroke-width="1.6"/><path d="M6 6h2M12 6h2M6 10h2M12 10h2M8 19v-4h4v4" stroke="#fff" stroke-width="1.6"/></svg>
    <div><h4>Hotels Houses</h4><p>Sure to make you think about a holiday when you book a room with views over the bay.</p><div class="more">More details</div></div>
  </div>
  <div class="feature">
    <svg width="24" height="18" viewBox="0 0 24 18"><path d="M2 12V8L5 3H19L22 8V12Z" fill="none" stroke="#fff" stroke-width="1.6"/><circle cx="7" cy="14" r="2.3" fill="#fff"/><circle cx="17" cy="14" r="2.3" fill="#fff"/></svg>
    <div><h4>Rental Vehicles</h4><p>Sure to make you think about a holiday when you drive the coast roads at your own pace.</p><div class="more">More details</div></div>
  </div>
</section>

<footer class="site-footer">
  <div class="mileage">
    <div class="badge"></div>
    <div>
      <h5>Mileage program</h5>
      <p>Earn points on every tour and hotel you book with us, then spend them on your next island trip.</p>
      <span class="btn-solid">CALL TO ACTION</span>
    </div>
  </div>
  <div class="col narrow"><h5>COMPANY</h5><ul><li>About</li><li>Careers</li><li>Press</li><li>Blog</li><li>Partners</li><li>Contact</li></ul></div>
  <div class="col narrow"><h5>SUPPORT</h5><ul><li>Help Center</li><li>Privacy Policy</li><li>Terms of Use</li><li>Listing Fees</li><li>Payments</li></ul></div>
  <div class="col narrow"><h5>SITES</h5><ul><li>News</li><li>Travel</li><li>Activities</li><li>Shop &amp; Dine</li><li>Store</li></ul></div>
  <div class="col search"><h5>SEARCH THE PLACES</h5><div class="input">Type Your Place...</div><div class="input">Type Your Keywords...</div><span class="btn-solid">SEARCH</span></div>
</footer>
<div class="legal">
  <span>© CALDERA KEY 2015. ALL RIGHTS RESERVED.</span>
  <span class="social">CONNECT WITH US <i></i><i></i><i></i><i></i><i></i></span>
</div>

</body>
</html>
```